Oil and Gas Exploration and Production company needs a business card design

We need a business card design using our logo and colors in the logo. We want a mainstream design.

```html
<!DOCTYPE html>
<html lang="en">
<head>
<meta charset="utf-8">
<title>Tolmec Oil &amp; Gas – Business Card</title>
<link href="https://fonts.googleapis.com/css2?family=Work+Sans:wght@400;500;700&display=swap" rel="stylesheet">
<style>
  :root {
    --gold: #c9962e;
    --black: #141414;
    --white: #ffffff;
    --ink: #1a1a1a;
    --backdrop: #2a2c2f;
  }
  * { margin: 0; padding: 0; box-sizing: border-box; }
  html, body { width: 1200px; height: 738px; overflow: hidden; }
  body {
    background: var(--backdrop);
    font-family: "Work Sans", Arial, sans-serif;
    display: flex;
    align-items: center;
    justify-content: center;
    gap: 60px;
  }
  .card {
    width: 500px;
    height: 286px;
    position: relative;
    overflow: hidden;
  }
  /* Front */
  .card-front {
    background: var(--black);
    display: flex;
    align-items: center;
    justify-content: center;
  }
  .brand {
    display: flex;
    align-items: center;
    gap: 12px;
    font-weight: 700;
    letter-spacing: 0.5px;
  }
  .brand-dot {
    border-radius: 50%;
    background: var(--gold);
    flex: none;
  }
  .card-front .brand { font-size: 38px; color: var(--white); }
  .card-front .brand-dot { width: 30px; height: 30px; }

  /* Back */
  .card-back { background: var(--white); color: var(--ink); }
  .card-back .brand {
    position: absolute;
    left: 30px;
    top: 44px;
    font-size: 25px;
    color: var(--ink);
    gap: 9px;
  }
  .card-back .brand-dot { width: 20px; height: 20px; }
  .person {
    position: absolute;
    right: 30px;
    top: 46px;
    text-align: right;
  }
  .person-name { font-size: 22px; font-weight: 500; color: var(--gold); line-height: 1.1; }
  .person-title { font-size: 10px; font-weight: 500; letter-spacing: 0.5px; }
  .divider {
    position: absolute;
    left: 30px;
    right: 30px;
    top: 104px;
    height: 1.5px;
    background: var(--gold);
  }
  .contact {
    position: absolute;
    left: 30px;
    top: 116px;
    list-style: none;
    font-size: 13px;
    line-height: 19px;
  }
  .contact li { display: flex; align-items: center; gap: 8px; }
  .contact svg { width: 10px; height: 10px; fill: var(--gold); flex: none; }
  .contact .accent { color: var(--gold); }
  .wave { position: absolute; left: 0; top: 0; width: 500px; height: 286px; }
  .address {
    position: absolute;
    right: 30px;
    bottom: 28px;
    color: var(--white);
    font-size: 12.5px;
    font-style: normal;
    line-height: 17px;
    text-align: right;
  }
</style>
</head>
<body>
  <section class="card card-front">
    <div class="brand"><span class="brand-dot"></span>Tolmec Oil &amp; Gas</div>
  </section>

  <section class="card card-back">
    <svg class="wave" viewBox="0 0 500 286" aria-hidden="true">
      <path d="M0 212 C120 250 210 236 300 196 C380 160 440 146 500 146 L500 286 L0 286 Z" fill="var(--gold)"/>
      <path d="M0 240 C130 270 212 256 302 214 C382 176 442 162 500 160 L500 286 L0 286 Z" fill="var(--white)"/>
      <path d="M0 246 C130 276 215 262 305 220 C385 182 445 168 500 166 L500 286 L0 286 Z" fill="var(--black)"/>
    </svg>

    <div class="brand"><span class="brand-dot"></span>Tolmec Oil &amp; Gas</div>

    <div class="person">
      <div class="person-name">Dale Hartwell</div>
      <div class="person-title">CFO</div>
    </div>

    <div class="divider"></div>

    <ul class="contact">
      <li>
        <svg viewBox="0 0 24 24"><path d="M6.6 10.8a15 15 0 0 0 6.6 6.6l2.2-2.2a1 1 0 0 1 1-.25 11.4 11.4 0 0 0 3.6.57 1 1 0 0 1 1 1V20a1 1 0 0 1-1 1A17 17 0 0 1 3 4a1 1 0 0 1 1-1h3.5a1 1 0 0 1 1 1c0 1.25.2 2.45.57 3.57a1 1 0 0 1-.25 1z"/></svg>
        (555) 014-2273
      </li>
      <li>
        <svg viewBox="0 0 24 24"><path d="M2 5h20v14H2z M4 7v.5l8 5 8-5V7z" fill-rule="evenodd"/></svg>
        info@tolmecoil.com
      </li>
      <li>
        <svg viewBox="0 0 24 24"><path d="M12 2a10 10 0 1 0 0 20 10 10 0 0 0 0-20zm0 2c.9 1.2 1.6 2.9 1.9 5h-3.8c.3-2.1 1-3.8 1.9-5zM4.3 11h3.8a16 16 0 0 0 0 2H4.3a8 8 0 0 1 0-2zm5.8 0h3.8a14 14 0 0 1 0 2h-3.8a14 14 0 0 1 0-2zm5.8 0h3.8a8 8 0 0 1 0 2h-3.8a16 16 0 0 0 0-2zM12 20c-.9-1.2-1.6-2.9-1.9-5h3.8c-.3 2.1-1 3.8-1.9 5z"/></svg>
        <span>www.<span class="accent">tolmecoil</span>.com</span>
      </li>
    </ul>

    <address class="address">
      2450 W Meridian Ave,<br>Amarillo, Texas us
    </address>
  </section>
</body>
</html>
```